Moravel Aesthetic Doctor

I require an elegant, luxurious looking business card for my aesthetic business. I am a doctor and that will set me aside from competitors. I am planning to provide home and spa based treatments to clients with high expectations. I have attached my logo.

```html
<!DOCTYPE html>
<html lang="en">
<head>
<meta charset="utf-8">
<title>Moravel Aesthetic Doctor – Business Card</title>
<link rel="stylesheet" href="https://fonts.googleapis.com/css2?family=Cormorant+Garamond:wght@400;500&family=Marcellus&family=Roboto:wght@300;400&display=swap">
<style>
  :root {
    --backdrop: #dcd7cf;
    --card: #eef1f2;
    --card-edge: #d6dbde;
    --wordmark-grey: #7e8995;
    --brand-blue: #3a97d0;
    --ink: #2f3338;
    --icon-grey: #555c63;
    --art-light: #bfe0f1;
    --art-mid: #3fa4d6;
    --art-deep: #1c6f9c;
  }
  * { margin: 0; padding: 0; box-sizing: border-box; }
  html, body {
    width: 1200px;
    height: 1054px;
    overflow: hidden;
    background: var(--backdrop);
  }
  .card {
    position: absolute;
    left: 100px;
    top: 227px;
    width: 1000px;
    height: 600px;
    border-radius: 22px;
    background: var(--card);
    border: 1px solid var(--card-edge);
    box-shadow: 0 18px 40px rgba(0,0,0,0.12);
    overflow: hidden;
  }
  .brand-art {
    position: absolute;
    left: 540px;
    top: 0;
    right: 0;
    bottom: 0;
    background: radial-gradient(ellipse 62% 58% at 62% 46%, var(--art-mid) 0%, var(--art-deep) 50%, var(--art-light) 82%, rgba(238,241,242,0) 100%);
    opacity: 0.85;
  }
  .wordmark {
    position: absolute;
    left: 41px;
    top: 60px;
    font-family: "Cormorant Garamond", serif;
    font-weight: 400;
    font-size: 96px;
    line-height: 1;
    letter-spacing: 0;
    color: var(--wordmark-grey);
  }
  .tagline {
    position: absolute;
    left: 43px;
    top: 156px;
    font-family: "Marcellus", serif;
    font-size: 36px;
    letter-spacing: 2px;
    color: var(--brand-blue);
  }
  .doctor-name {
    position: absolute;
    left: 41px;
    top: 292px;
    font-family: "Roboto", sans-serif;
    font-weight: 300;
    font-size: 36px;
    color: var(--ink);
  }
  .doctor-name .postnominals {
    font-size: 18px;
    font-weight: 400;
    color: var(--brand-blue);
    margin-left: 6px;
  }
  .qualification {
    position: absolute;
    left: 42px;
    top: 342px;
    font-family: "Roboto", sans-serif;
    font-weight: 400;
    font-size: 23px;
    line-height: 33px;
    color: var(--brand-blue);
  }
  .contact-list {
    position: absolute;
    left: 48px;
    top: 453px;
    list-style: none;
    font-family: "Roboto", sans-serif;
    font-size: 21px;
    color: var(--ink);
  }
  .contact-list li {
    display: flex;
    align-items: center;
    height: 38px;
  }
  .contact-icon {
    width: 18px;
    height: 18px;
    margin-right: 14px;
    fill: var(--icon-grey);
  }
  .divider { margin: 0 10px; color: var(--icon-grey); }
  .social-dot {
    display: inline-block;
    width: 21px;
    height: 21px;
    border-radius: 50%;
    background: var(--icon-grey);
    margin-left: 7px;
  }
  .social-dot:first-of-type { margin-left: 10px; }
</style>
</head>
<body>
  <div class="card">
    <div class="brand-art" role="img" aria-label="Brand decoration area in flowing shades of blue"></div>

    <div class="wordmark">MORAVEL</div>
    <div class="tagline">AESTHETIC DOCTOR</div>

    <div class="doctor-name">Dr Elise Varnholt<span class="postnominals">MRCPCH MD</span></div>
    <div class="qualification">Australasian Diploma of<br>Aesthetic Medicine</div>

    <ul class="contact-list">
      <li>
        <svg class="contact-icon" viewBox="0 0 24 24" aria-hidden="true"><path d="M6.6 10.8a15.1 15.1 0 0 0 6.6 6.6l2.2-2.2a1 1 0 0 1 1-.25 11.4 11.4 0 0 0 3.6.57 1 1 0 0 1 1 1V20a1 1 0 0 1-1 1A17 17 0 0 1 3 4a1 1 0 0 1 1-1h3.5a1 1 0 0 1 1 1c0 1.25.2 2.45.57 3.57a1 1 0 0 1-.25 1z"/></svg>
        0800 555 014
      </li>
      <li>
        <svg class="contact-icon" viewBox="0 0 24 24" aria-hidden="true"><path d="M2 5h20v14H2zM4 7v.3l8 5.7 8-5.7V7l-8 5.6z" fill-rule="evenodd"/></svg>
        elise@moravel.co.nz
      </li>
      <li>
        <svg class="contact-icon" viewBox="0 0 24 24" aria-hidden="true"><circle cx="12" cy="12" r="9" fill="none" stroke="#555c63" stroke-width="2"/><ellipse cx="12" cy="12" rx="4" ry="9" fill="none" stroke="#555c63" stroke-width="1.6"/><path d="M3 12h18" stroke="#555c63" stroke-width="1.6"/></svg>
        www.moravel.co.nz<span class="divider">|</span>Follow us on:<span class="social-dot"></span><span class="social-dot"></span>
      </li>
    </ul>
  </div>
</body>
</html>
```